Bramblewood Card Company Business Cards

We are a trading card store with Glimmorax, sports and other TCG cards, we need a business card design that encompasses a clean cut, modern style with a retro flare. website is bramblewoodcardco.com for reference. Can utilize a comic book era feel or a more modern outdoor feel to utilize the "Pacific Northwest" elements of tress, mountains, etc.

Industry/Entity Type

Trading cards and collectibles

Contact Information for Business Card

business name, email address, phone number, name, owner job title

Font styles to use
Sans Serif

```html
<!DOCTYPE html>
<html lang="en">
<head>
<meta charset="utf-8">
<title>Bramblewood Card Company – Business Cards</title>
<link href="https://fonts.googleapis.com/css2?family=Montserrat:wght@400;500;700;800&display=swap" rel="stylesheet">
<style>
  :root {
    --backdrop: #26282b;
    --card-white: #ffffff;
    --brand-blue: #1fb8dc;
    --brand-grey: #6b6c6e;
    --ink-dark: #2e2f31;
    --ink-light: #ffffff;
  }
  html, body {
    margin: 0;
    width: 1200px;
    height: 900px;
    overflow: hidden;
    background: var(--backdrop);
    font-family: "Montserrat", sans-serif;
  }
  .sheet {
    position: relative;
    width: 1200px;
    height: 900px;
  }
  .card {
    position: absolute;
    top: 300px;
    width: 525px;
    height: 300px;
    overflow: hidden;
    border-radius: 3px;
    box-shadow: 0 10px 30px rgba(0,0,0,.45);
  }
  .card--front { left: 50px; background: var(--card-white); }
  .card--back  { left: 625px; background: var(--brand-blue); }

  .front-shapes { position: absolute; inset: 0; }

  .holder {
    position: absolute;
    left: 34px;
    top: 30px;
  }
  .holder__name {
    margin: 0;
    color: var(--brand-blue);
    font-weight: 700;
    font-size: 21px;
    letter-spacing: 1px;
    text-transform: uppercase;
  }
  .holder__title {
    margin: 2px 0 0;
    color: var(--ink-dark);
    font-size: 12px;
    font-weight: 500;
  }

  .contact {
    position: absolute;
    left: 34px;
    top: 124px;
    margin: 0;
    padding: 0;
    list-style: none;
    color: var(--ink-light);
    font-size: 12px;
    line-height: 19px;
  }
  .contact li { display: flex; align-items: center; gap: 7px; }
  .contact svg { width: 10px; height: 10px; fill: var(--ink-light); flex: none; }
  .contact .no-icon { padding-left: 17px; }

  .brand-name {
    position: absolute;
    margin: 0;
    color: var(--ink-light);
    font-weight: 800;
    text-transform: uppercase;
    text-align: center;
    letter-spacing: 1.5px;
    line-height: 1.15;
  }
  .card--front .brand-name {
    right: 32px;
    top: 196px;
    width: 180px;
    font-size: 16px;
  }
  .card--back .brand-name {
    left: 0;
    right: 0;
    top: 118px;
    font-size: 26px;
  }
</style>
</head>
<body>
<main class="sheet">

  <section class="card card--front" aria-label="Business card front">
    <svg class="front-shapes" viewBox="0 0 525 300" preserveAspectRatio="none" aria-hidden="true">
      <polygon points="0,110 300,110 420,300 0,300" fill="var(--brand-blue)"/>
      <polygon points="0,260 0,300 30,300" fill="var(--card-white)"/>
      <polygon points="300,165 525,165 525,300 385,300" fill="var(--brand-grey)"/>
      <rect x="494" y="0" width="31" height="300" fill="var(--card-white)"/>
    </svg>

    <header class="holder">
      <h1 class="holder__name">Dorian Vale</h1>
      <p class="holder__title">CEO/Founder</p>
    </header>

    <ul class="contact">
      <li class="no-icon">P.O. Box 4718 Fern Lane</li>
      <li class="no-icon">Cedar Falls WA 98071</li>
      <li>
        <svg viewBox="0 0 10 10"><path d="M2 0.5 3.6 2.6 2.7 3.7C3.3 5 4.9 6.6 6.3 7.3L7.4 6.4 9.5 8 8.6 9.5C4.5 9.3 0.7 5.5 0.5 1.4Z"/></svg>
        (360) 555 0147
      </li>
      <li>
        <svg viewBox="0 0 10 10"><path d="M0 2h10v6H0z" opacity=".35"/><path d="M0 2h10L5 6z"/></svg>
        info@bramblewoodcardco.com
      </li>
      <li>
        <svg viewBox="0 0 10 10"><circle cx="5" cy="5" r="4.5"/></svg>
        www.bramblewoodcardco.com
      </li>
    </ul>

    <p class="brand-name">Bramblewood<br>Card Company</p>
  </section>

  <section class="card card--back" aria-label="Business card back">
    <p class="brand-name">Bramblewood<br>Card Company</p>
  </section>

</main>
</body>
</html>
```